5 website banners (slides show)

We need 5 website sliding banners created for a website all about internet safety. The topics for each banner are:

Cyberbullying
Fraud
seniors
social networking

Sizes: 953 pixels x 281 pixels

I have stock images to use or feel free to use your own or one I can purchase from pixelharbor.example.

Industry/Entity Type

Internet

```html
<!DOCTYPE html>
<html lang="en">
<head>
<meta charset="utf-8">
<title>Social Networking – Internet Safety Banner</title>
<link rel="stylesheet" href="https://fonts.googleapis.com/css2?family=Open+Sans:wght@300;400&display=swap">
<style>
  :root {
    --bg: #f8f8f8;
    --bg-edge: #f1f1f1;
    --title: #2b879c;
    --body-text: #2f3133;
    --photo-dark: #5a6e8c;
    --photo-mid: #a9b7c9;
    --photo-light: #dfe3ea;
    --deco: #e6e6e6;
  }
  * { margin: 0; padding: 0; box-sizing: border-box; }
  html, body {
    width: 1200px;
    height: 354px;
    overflow: hidden;
    background: var(--bg);
  }
  .banner {
    position: relative;
    width: 1200px;
    height: 354px;
    background: radial-gradient(ellipse at 40% 45%, #fbfbfb 0%, var(--bg) 55%, var(--bg-edge) 100%);
    overflow: hidden;
    font-family: "Open Sans", Arial, sans-serif;
  }
  .banner__photo {
    position: absolute;
    left: 19px;
    top: 63px;
    width: 554px;
    height: 234px;
    border-radius: 6px;
    background: linear-gradient(180deg, var(--photo-light) 0%, var(--photo-mid) 35%, var(--photo-dark) 75%, var(--photo-mid) 100%);
    opacity: 0.85;
  }
  .banner__decoration {
    position: absolute;
    right: 0;
    bottom: 0;
    width: 360px;
    height: 170px;
    background: radial-gradient(ellipse at 60% 70%, var(--deco) 0%, rgba(230,230,230,0.5) 45%, rgba(248,248,248,0) 75%);
  }
  .banner__copy {
    position: absolute;
    right: 76px;
    top: 92px;
    width: 560px;
    text-align: right;
  }
  .banner__title {
    font-weight: 300;
    font-size: 60px;
    line-height: 1;
    color: var(--title);
    letter-spacing: 0.2px;
  }
  .banner__text {
    margin-top: 18px;
    font-weight: 400;
    font-size: 16.5px;
    line-height: 29px;
    color: var(--body-text);
  }
</style>
</head>
<body>
  <section class="banner">
    <div class="banner__decoration" role="img" aria-label="Faint scattered thumbs-up signs in light grey"></div>
    <div class="banner__photo" role="img" aria-label="A row of eleven children standing side by side, each looking down at a phone or tablet"></div>
    <div class="banner__copy">
      <h1 class="banner__title">Social Networking</h1>
      <p class="banner__text">Nullam congue augue magna, ac pretium odio suscipit et. Viva<br>condimentum luctusmus porttitor quis lorem quis ornare.</p>
    </div>
  </section>
</body>
</html>
```